Website Banner Redesign for Kelvra Cargo Depot

Business Name:
KELVRA CARGO DEPOT

About Us:
- We’re a proudly Australian company that designs and builds tough, reliable toolboxes for Utes, Trucks, and Campervans. Our products are made to handle harsh conditions and are trusted by tradies, off-roaders, and professional fleets across the country.

Project Goal:
- We want to refresh our homepage and category banners with bold, modern designs that better showcase our products and value proposition.

Why We’re Updating:
Our current banners show the products well, but we want to improve:
Visual impact and hierarchy
- Readability of text (especially on mobile)
- Clearer calls-to-action (CTAs)
- Brand messaging around “Built Tough”, “Aussie Made”, and “Custom Fit-Outs”

Target Audience:
- Tradespeople
- 4x4 & off-road enthusiasts
- Caravan & camping community
- Ute/Truck/Caravan dealerships
- Fleet and commercial buyers

Design Style We Want:
- Bold, confident, rugged
- Clean layout with clear focal points
- Strong product imagery (we’ll supply photos)
- Use of brand colors: Black, White, Red, Grey
- Professional, not too busy or cluttered

Banner Uses:
- Homepage hero banner
- Category landing pages

UTE TOOLBOXES - https://www.kelvracargo.com.au/aluminium-toolboxes/
Truck Boxes - https://www.kelvracargo.com.au/truck-toolboxes/
Canopies - https://www.kelvracargo.com.au/canopy/
Dog Boxes - https://www.kelvracargo.com.au/dog-boxes/
CAMPER BOXES - https://www.kelvracargo.com.au/camper-toolboxes/
Accessories - https://www.kelvracargo.com.au/accessories/

- Can be reused for desktop and mobile

Inspiration Style:
Think: 4x4 accessory brands, tough tradie gear, or clean eCommerce landing banners from premium auto suppliers.

Target Market(s)

All in Brief Above

Industry/Entity Type

Retail

Requirements
Must have
• A banner using our products only. A banner for each category, and 2 alternate banners for the home page.
Nice to have
• I have added some designs which i like..... Please take a look and take inspiration from them.

```html
<!DOCTYPE html>
<html lang="en">
<head>
<meta charset="utf-8">
<title>Kelvra Cargo Depot – Truck Boxes Banner</title>
<link rel="stylesheet" href="https://fonts.googleapis.com/css2?family=Bebas+Neue&family=Open+Sans:ital,wght@0,400;0,600;0,700;1,400&family=Rubik:wght@500;700&display=swap">
<style>
  :root {
    --stage: #505050;
    --black: #0b0b0b;
    --steel-dark: #1c1c1c;
    --steel-mid: #8a8a8a;
    --steel-light: #e6e6e6;
    --fog-light: #f2f2f2;
    --fog-mid: #b9b9b9;
    --fog-dark: #6f6f6f;
    --brand-red: #8e1434;
    --brand-red-edge: #c23a5c;
    --nav-red: #a51d4a;
    --nav-yellow: #f5cc00;
    --white: #ffffff;
    --ink: #222222;
    --ink-soft: #444444;
    --review-green: #34a853;
  }
  * { margin: 0; padding: 0; box-sizing: border-box; }
  html, body {
    width: 1200px; height: 1200px; overflow: hidden;
    background: var(--stage);
    position: relative;
  }

  /* ---------- Banner component ---------- */
  .banner {
    position: absolute;
    width: 1042px; height: 292px;
    overflow: hidden;
    background: radial-gradient(ellipse 60% 60% at 50% 58%, var(--fog-light) 0%, var(--fog-mid) 55%, var(--fog-dark) 100%);
  }
  .banner--standalone { left: 78px; top: 130px; box-shadow: 0 30px 40px -24px rgba(0,0,0,0.7); }
  .side-rail {
    position: absolute; top: 0; width: 50px; height: 100%;
    background: linear-gradient(90deg, var(--black) 0%, var(--steel-dark) 45%, var(--steel-mid) 72%, var(--black) 100%);
  }
  .side-rail--left { left: 0; }
  .side-rail--right { right: 0; transform: scaleX(-1); }
  .side-rail svg { position: absolute; inset: 0; }
  .product-photo {
    position: absolute;
    left: 234px; top: 34px;
    width: 512px; height: 232px;
    background: linear-gradient(180deg, #fbfbfb 0%, #e4e4e4 55%, #c9c9c9 100%);
    border-radius: 3px;
    box-shadow: 0 8px 18px rgba(0,0,0,0.25);
  }
  .category-tag {
    position: absolute;
    left: 50px; top: 195px;
    width: 306px; height: 65px;
    background: var(--black);
    clip-path: polygon(0 0, 88% 0, 100% 100%, 0 100%);
  }
  .category-tag__title {
    position: absolute; left: 14px; top: 4px;
    font-family: "Bebas Neue", sans-serif;
    font-weight: 400;
    font-size: 62px; line-height: 62px;
    color: var(--steel-light);
  }
  .cta-button {
    position: absolute;
    left: 793px; top: 224px;
    width: 131px; height: 39px;
    border-radius: 20px;
    background: var(--brand-red);
    border: 2px solid var(--brand-red-edge);
    display: flex; align-items: center; justify-content: center;
    font-family: "Bebas Neue", sans-serif;
    font-size: 33px; line-height: 1;
    color: var(--white);
    padding-top: 3px;
    text-decoration: none;
  }

  /* ---------- Website preview ---------- */
  .site-preview {
    position: absolute;
    left: 78px; top: 536px;
    width: 1042px; height: 526px;
    overflow: hidden;
    background: var(--white);
    box-shadow: 0 30px 40px -24px rgba(0,0,0,0.7);
    font-family: "Open Sans", sans-serif;
  }
  .site-header {
    position: absolute; left: 0; top: 0; width: 100%; height: 42px;
    background: var(--black);
  }
  .site-header__brand {
    position: absolute; left: 210px; top: 6px;
    width: 116px; height: 30px;
    border: 1.5px solid var(--white); border-radius: 3px;
    display: flex; align-items: center; justify-content: center;
    font-family: "Open Sans", sans-serif; font-weight: 700;
    font-size: 8.5px; color: var(--white); letter-spacing: 0.3px;
  }
  .site-search {
    position: absolute; left: 487px; top: 11px;
    width: 235px; height: 20px;
    background: var(--white); border-radius: 2px;
    font-size: 7.5px; color: #999; padding: 5px 10px;
  }
  .site-search svg { position: absolute; right: 8px; top: 5px; }
  .site-cart {
    position: absolute; left: 732px; top: 14px;
    font-size: 8px; color: var(--white);
    display: flex; align-items: center; gap: 6px;
  }
  .site-nav {
    position: absolute; left: 0; top: 42px; width: 100%; height: 31px;
    background: var(--nav-red);
    font-size: 7.5px; color: var(--white); font-weight: 600;
  }
  .site-nav__category {
    position: absolute; left: 196px; top: 0; width: 146px; height: 31px;
    background: var(--nav-yellow); color: var(--ink);
    font-size: 8.5px; font-weight: 700;
    display: flex; align-items: center; justify-content: space-between;
    padding: 0 10px;
  }
  .site-nav__links { position: absolute; left: 359px; top: 11px; display: flex; gap: 9px; }
  .site-nav__util { position: absolute; top: 11px; display: flex; align-items: center; gap: 3px; }
  .site-preview .banner { left: 0; top: 73px; }
  .site-content {
    position: absolute; left: 0; top: 366px; width: 100%;
    text-align: center; color: var(--ink-soft);
  }
  .site-content__title {
    font-family: "Rubik", sans-serif; font-weight: 700;
    font-size: 14px; color: var(--ink); letter-spacing: 0.6px;
    margin-top: 12px;
  }
  .site-content__text { width: 640px; margin: 0 auto; font-size: 6.8px; line-height: 11px; }
  .site-content__text--quote { font-style: italic; margin-top: 6px; }
  .site-content__text p + p { margin-top: 5px; }
  .site-content__text em { color: var(--nav-red); font-style: normal; font-weight: 700; }
  .site-content__sub {
    font-family: "Rubik", sans-serif; font-weight: 700;
    font-size: 11.5px; color: var(--ink); letter-spacing: 0.6px;
    margin-top: 10px;
  }
  .site-content__rule { width: 638px; height: 1px; background: #ddd; margin: 6px auto 0; }
  .collection-row { position: absolute; left: 200px; top: 508px; display: flex; gap: 8px; }
  .collection-row__item {
    width: 155px; height: 24px; background: var(--black); color: var(--white);
    border-radius: 3px 3px 0 0;
    font-size: 8px; font-weight: 600; text-align: center; padding-top: 10px;
  }
  .review-badge {
    position: absolute; left: 0; top: 484px; width: 112px; height: 40px;
    background: var(--white); border-top: 2px solid var(--review-green);
  }
  .review-badge span {
    position: absolute; left: 4px; top: 11px; width: 18px; height: 18px;
    border-radius: 50%; border: 3px solid var(--review-green);
  }
  .chat-card {
    position: absolute; left: 871px; top: 418px; width: 157px; height: 52px;
    background: var(--white); border-radius: 4px;
    box-shadow: 0 2px 8px rgba(0,0,0,0.2);
    font-size: 8px; line-height: 12px; color: var(--ink);
    padding: 12px 10px 0 45px;
  }
  .chat-card__icon {
    position: absolute; left: 13px; top: 14px; width: 24px; height: 24px;
    border-radius: 50%; background: var(--brand-red);
  }
  .chat-pill {
    position: absolute; left: 960px; top: 485px; width: 67px; height: 25px;
    border-radius: 13px; background: var(--nav-red); color: var(--white);
    font-size: 8.5px; font-weight: 700;
    display: flex; align-items: center; justify-content: center; gap: 5px;
  }
</style>
</head>
<body>
  <!-- Standalone banner -->
  <section class="banner banner--standalone" aria-label="Kelvra Cargo Depot truck boxes banner">
    <div class="side-rail side-rail--left">
      <svg width="50" height="292" viewBox="0 0 50 292"><path d="M36 0 V100 L50 118 V172 L36 190 V292" fill="none" stroke="#d9d9d9" stroke-width="3"/></svg>
    </div>
    <div class="side-rail side-rail--right">
      <svg width="50" height="292" viewBox="0 0 50 292"><path d="M36 0 V100 L50 118 V172 L36 190 V292" fill="none" stroke="#d9d9d9" stroke-width="3"/></svg>
    </div>
    <div class="product-photo" role="img" aria-label="Two white aluminium truck boxes: one with gullwing lid open showing shelves and drawers, one with roller shutter door"></div>
    <div class="category-tag"><h1 class="category-tag__title">Truck Boxes</h1></div>
    <a class="cta-button" href="https://www.kelvracargo.com.au/truck-toolboxes/">Click Here</a>
  </section>

  <!-- Banner in website context -->
  <section class="site-preview" aria-label="Banner shown on the Kelvra Cargo Depot homepage">
    <header class="site-header">
      <div class="site-header__brand">KELVRA CARGO DEPOT</div>
      <div class="site-search">Search...
        <svg width="10" height="10" viewBox="0 0 10 10"><circle cx="4" cy="4" r="3.2" fill="none" stroke="#a51d4a" stroke-width="1.2"/><path d="M6.4 6.4 L9 9" stroke="#a51d4a" stroke-width="1.2"/></svg>
      </div>
      <div class="site-cart">
        <svg width="16" height="12" viewBox="0 0 16 12"><path d="M1 1 H4 L6 8 H13 L15 3 H5" fill="none" stroke="#fff" stroke-width="1.2"/><circle cx="7" cy="10.5" r="1" fill="#fff"/><circle cx="12" cy="10.5" r="1" fill="#fff"/></svg>
        <span>MY CART&nbsp;&nbsp; $0.00 ▾</span>
      </div>
    </header>
    <nav class="site-nav">
      <div class="site-nav__category"><span>Shop By Category</span><span>☰</span></div>
      <div class="site-nav__links"><span>PRODUCTS</span><span>ABOUT US</span><span>CONTACT US</span><span>SALE</span></div>
      <div class="site-nav__util" style="left:706px">✆ 1300 555 KCD</div>
      <div class="site-nav__util" style="left:784px">♡ Wishlists</div>
      <div class="site-nav__util" style="left:846px">Login | Register</div>
    </nav>

    <div class="banner" aria-label="Truck boxes banner">
      <div class="side-rail side-rail--left">
        <svg width="50" height="292" viewBox="0 0 50 292"><path d="M36 0 V100 L50 118 V172 L36 190 V292" fill="none" stroke="#d9d9d9" stroke-width="3"/></svg>
      </div>
      <div class="side-rail side-rail--right">
        <svg width="50" height="292" viewBox="0 0 50 292"><path d="M36 0 V100 L50 118 V172 L36 190 V292" fill="none" stroke="#d9d9d9" stroke-width="3"/></svg>
      </div>
      <div class="product-photo" role="img" aria-label="Two white aluminium truck boxes: one with gullwing lid open showing shelves and drawers, one with roller shutter door"></div>
      <div class="category-tag"><h2 class="category-tag__title">Truck Boxes</h2></div>
      <a class="cta-button" href="https://www.kelvracargo.com.au/truck-toolboxes/">Click Here</a>
    </div>

    <div class="site-content">
      <h2 class="site-content__title">TOOLBOXES FOR UTES</h2>
      <div class="site-content__text site-content__text--quote">"Kelvra Cargo Depot has one of the largest and most comprehensive range of premium aluminium flat plate toolboxes for utes in Australia."</div>
      <div class="site-content__text" style="margin-top:5px">
        <p>Our ute toolboxes come in a wide range of sizes and multiple configurations that can be fitted onto any ute or truck.</p>
        <p>At present, we provide ute toolboxes, aluminium gullwing canopy for ute, truck toolboxes, dog boxes, trailer toolboxes, and other ute and truck aluminium toolboxes to our customers. Shop with us and promote local businesses online. If you have any suggestions you think can improve our toolbox business, please feel free to <em>call</em> or <em>write</em> to the Kelvra team.</p>
      </div>
      <h3 class="site-content__sub">OUR COLLECTION</h3>
      <div class="site-content__rule"></div>
    </div>

    <div class="collection-row">
      <div class="collection-row__item">White Pro Series</div>
      <div class="collection-row__item">Black Pro Series</div>
      <div class="collection-row__item">Full Lid Toolboxes</div>
      <div class="collection-row__item">Half Lid Toolboxes</div>
    </div>

    <div class="review-badge" aria-label="Customer review badge"><span></span></div>

    <div class="chat-card"><div class="chat-card__icon"></div>Have a question? Chat with us here.</div>
    <div class="chat-pill">
      <svg width="10" height="10" viewBox="0 0 10 10"><circle cx="5" cy="5" r="4.5" fill="#fff"/></svg>
      Text us
    </div>
  </section>
</body>
</html>
```